Golf Tournament Flyer and Header Needed

Non-profit needs a flyer for their benefit golf tournament - "Wild Socks Benefit Golf Classic"

Target Market(s)

Design and Construction industry professionals

Industry/Entity Type

Design and Construction

Colors

Designer to choose colors to be used in the design.

Requirements
Must have
• Date: September 22, 2021, 8:00 AM Shotgun Start, Location: Brookmere Links. O-VardeX Logo
Nice to have
• Would like image of golfers in crazy pants incorporated.

```html
<!DOCTYPE html>
<html lang="en">
<head>
<meta charset="utf-8">
<title>Wild Socks Benefit Golf Classic</title>
<link rel="stylesheet" href="https://fonts.googleapis.com/css2?family=Oswald:wght@500;600&family=Lato:wght@400;700&display=swap">
<style>
  :root {
    --page: #eef1ec;
    --card: #ffffff;
    --frame: #b9c0e0;
    --navy: #2e3f8f;
    --green: #7da63a;
    --deep-green: #4e8a2a;
    --ink: #333333;
    --sky: #8fbbef;
    --turf: #6f9a45;
  }
  * { margin: 0; padding: 0; box-sizing: border-box; }
  html, body { width: 1200px; height: 800px; overflow: hidden; background: var(--page); }
  .canvas { position: relative; width: 1200px; height: 800px; }
  .flyer {
    position: absolute; left: 20px; top: 103px; width: 1160px; height: 593px;
    background: var(--card); overflow: hidden;
    box-shadow: 0 2px 10px rgba(0,0,0,0.08);
  }
  .flyer__photo { position: absolute; inset: 0; width: 1160px; height: 593px; }
  .flyer__frame {
    position: absolute; left: 32px; top: 25px; right: 24px; bottom: 25px;
    border: 1px solid var(--frame);
  }
  .event {
    position: absolute; left: 720px; width: 390px; top: 0; text-align: center;
  }
  .event__kicker {
    position: absolute; left: 0; right: 0; top: 144px;
    font-family: "Oswald", sans-serif; font-weight: 600; font-size: 23px;
    color: var(--deep-green); letter-spacing: 0.5px; line-height: 1;
  }
  .event__title {
    position: absolute; left: 0; right: 0; top: 176px;
    font-family: "Oswald", sans-serif; font-weight: 600; font-size: 36px;
    line-height: 1; letter-spacing: 0.5px; color: var(--navy);
  }
  .event__title-accent { color: var(--green); }
  .event__rule {
    position: absolute; left: 97px; width: 196px; border-top: 2px dashed #222;
  }
  .event__rule--top { top: 236px; }
  .event__rule--bottom { top: 306px; }
  .event__date {
    position: absolute; left: 0; right: 0; top: 251px;
    font-family: "Oswald", sans-serif; font-weight: 500; font-size: 34px;
    color: var(--ink); line-height: 1; word-spacing: 14px;
  }
  .event__date-sep { color: var(--navy); }
  .event__time, .event__place {
    position: absolute; left: 0; right: 0;
    font-family: "Lato", sans-serif; font-size: 14px; color: var(--ink);
  }
  .event__time { top: 322px; }
  .event__place { top: 342px; text-transform: uppercase; }
  .event__label { color: var(--navy); font-weight: 700; }
  .event__time strong { font-weight: 700; }
  .host {
    position: absolute; left: 0; right: 0; top: 420px;
    display: flex; justify-content: center; align-items: center; gap: 12px;
  }
  .host__square {
    width: 22px; height: 22px; background: var(--navy);
  }
  .host__name {
    font-family: "Oswald", sans-serif; font-weight: 600; font-size: 30px;
    color: var(--navy); line-height: 1; letter-spacing: 1px;
  }
</style>
</head>
<body>
<main class="canvas">
  <section class="flyer">
    <svg class="flyer__photo" viewBox="0 0 1160 593" role="img" aria-label="Photo of four golfers in white polos and blue diamond-pattern pants standing on a golf course">
      <defs>
        <linearGradient id="photo-tone" x1="0" y1="0" x2="0" y2="1">
          <stop offset="0" stop-color="#8fbbef"/>
          <stop offset="0.45" stop-color="#a9c4d8"/>
          <stop offset="0.7" stop-color="#7d9f6a"/>
          <stop offset="1" stop-color="#6f9a45"/>
        </linearGradient>
      </defs>
      <polygon points="0,0 740,0 390,593 0,593" fill="url(#photo-tone)"/>
    </svg>
    <div class="flyer__frame"></div>

    <div class="event">
      <p class="event__kicker">GOLF TOURNAMENT</p>
      <h1 class="event__title">WILD SOCKS <span class="event__title-accent">CLASSIC</span></h1>
      <div class="event__rule event__rule--top"></div>
      <p class="event__date">09 <span class="event__date-sep">|</span> 22 <span class="event__date-sep">|</span> 21</p>
      <div class="event__rule event__rule--bottom"></div>
      <p class="event__time"><strong>8:00 AM</strong> Shotgun Start</p>
      <p class="event__place"><span class="event__label">Location:</span> Brookmere Links.</p>

      <div class="host">
        <span class="host__square"></span>
        <p class="host__name">O-VARDEX</p>
      </div>
    </div>
  </section>
</main>
</body>
</html>
```